Website Design for a Project Management Consulting Business

I have a logo design already and now I need a website.
I am a project manager and run my own consulting business.
Currently I am under contract with 3 major Vantage 400 companies. I'd like a website I can direct current and future clients.
My job is running IT projects and working with developers to deliver business priorities.
The website should be professional and clean - I work IT projects and would like to incorporate that into any theme.
I'd like the site to have several page or breakoff links - sections would include : about me, about my services, a page to display all of my certification badges, another page to talk about highlights from past projects and so on.
Looking for a collaborative experience.

Industry/Entity Type

Vantage 400 Consulting Firm - Project Management

Coding

Coded - Design and coding required

Number of Pages Required

1 page

Font styles to use
Serif

Colors
0094D4
00A9DD
6FCCEA
C7EBF8
E9F6FB
EE7325
F08F49
F5BC92
FAE3D3
FDF4ED

Requirements
Must have
• Sections that are a must: About Me (bio), About My Services, About my Certifications and Credentials, Experience on Past Projects,
Nice to have
• I have added the logo below - I'd like to use the logo and have it prominent ; should be professional and inviting

```html
<!DOCTYPE html>
<html lang="en">
<head>
<meta charset="utf-8">
<title>Jordan Ellis — Keystone Delivery Partners, LLC</title>
<link href="https://fonts.googleapis.com/css2?family=Montserrat:wght@400;500;600;700;800;900&family=Playfair+Display:wght@700&display=swap" rel="stylesheet">
<style>
:root{
  --blue:#0094D4;
  --blue-2:#00A9DD;
  --sky:#6FCCEA;
  --ice:#C7EBF8;
  --mist:#E9F6FB;
  --orange:#EE7325;
  --orange-2:#F08F49;
  --peach:#F5BC92;
  --gold:#F6A623;
  --navy:#1C3E73;
  --ink:#1f2430;
  --white:#ffffff;
}
*{box-sizing:border-box;margin:0;padding:0}
html,body{width:1200px;height:3221px;overflow:hidden}
body{font-family:'Montserrat',sans-serif;color:var(--ink);background:var(--white);position:relative}
a{text-decoration:none;color:inherit}

/* header */
.site-header{position:absolute;top:0;left:0;width:1200px;height:72px;background:var(--white);z-index:3}
.brand{position:absolute;left:129px;top:19px;display:flex;align-items:center;gap:10px}
.brand-mark{width:32px;height:32px;background:var(--navy)}
.brand-name{font-weight:700;font-size:17px;letter-spacing:1.5px;color:var(--navy);line-height:1.05}
.main-nav{position:absolute;right:133px;top:0;height:72px;display:flex}
.main-nav a{display:flex;align-items:center;height:72px;font-size:14px;font-weight:500;color:var(--ink);margin-left:31px;position:relative}
.main-nav a.active{color:var(--orange);font-weight:700}
.main-nav a.active::before,.main-nav a.active::after{content:"";position:absolute;left:0;right:0;height:3px;background:var(--orange)}
.main-nav a.active::before{top:0}
.main-nav a.active::after{bottom:0}

/* hero */
.hero{position:absolute;top:72px;left:0;width:1200px;height:559px;background-color:var(--mist);
  background-image:linear-gradient(rgba(0,148,212,.07) 1px,transparent 1px),linear-gradient(90deg,rgba(0,148,212,.07) 1px,transparent 1px);
  background-size:24px 24px;overflow:hidden}
.hero-band{position:absolute;left:0;bottom:0;width:620px;height:34px;background:var(--sky);clip-path:polygon(0 0,100% 100%,0 100%)}
.eyebrow{position:absolute;left:132px;top:70px;display:flex;align-items:center}
.eyebrow-tag{background:var(--blue);color:var(--white);font-weight:800;font-size:14px;padding:4px 9px;border-right:4px solid var(--orange)}
.eyebrow-line{width:242px;height:3px;background:var(--blue);margin-left:28px}
.hero-name{position:absolute;left:135px;top:100px;font-size:52px;font-weight:800;color:var(--navy);letter-spacing:-.5px}
.hero-rule{position:absolute;left:136px;top:170px;width:116px;height:3px;background:var(--blue)}
.hero-copy{position:absolute;left:136px;top:204px;width:410px;font-size:13.6px;line-height:19px;color:var(--ink)}
.hero-copy p+p{margin-top:19px}
.btn-solid{display:inline-block;background:var(--orange);color:var(--white);font-weight:800;font-size:14px;text-align:center}
.hero .btn-solid{position:absolute;left:138px;top:395px;width:128px;height:43px;line-height:43px}
.hero-photo{position:absolute;left:560px;top:14px;width:500px;height:545px;border-radius:250px 250px 0 0;
  background:linear-gradient(180deg,#8c97a8 0%,#6d84a8 38%,#55709b 70%,#465f88 100%)}

/* section titles */
.section-title{position:absolute;left:50%;transform:translateX(-50%);font-weight:900;font-size:25px;padding:10px 18px;letter-spacing:.3px;white-space:nowrap}
.section-title::before,.section-title::after{content:"";position:absolute;top:0;bottom:0;width:18px;border:3px solid currentColor}
.section-title::before{left:0;border-right:none}
.section-title::after{right:0;border-left:none}
.section-title .accent{color:var(--orange)}

/* services */
.services{position:absolute;top:631px;left:0;width:1200px;height:968px;background:var(--blue);color:var(--white)}
.services .section-title{top:44px;color:var(--white)}
.services-wedge{position:absolute;left:0;top:942px;width:1200px;height:26px;background:var(--sky);clip-path:polygon(100% 0,100% 100%,0 0)}
.service{position:absolute;width:280px}
.service-icon{width:54px;height:54px;display:block}
.service-title{font-family:'Playfair Display',serif;font-weight:700;font-size:20px;line-height:23px;margin-top:33px}
.service-text{font-size:13.4px;line-height:17.6px;margin-top:24px}
.btn-outline{display:inline-block;border:2px solid var(--white);color:var(--white);font-weight:800;font-size:11.5px;padding:7px 11px;margin-top:22px}

/* projects */
.projects{position:absolute;top:1599px;left:0;width:1200px;height:980px;background:var(--white)}
.projects .section-title{top:23px;color:var(--blue)}
.project{position:absolute;width:306px;height:239px}
.project-label{position:absolute;left:0;top:12px;background:var(--white);font-size:13px;font-weight:500;padding:6px 8px 5px 5px}
.projects .btn-solid{position:absolute;left:520px;top:891px;width:185px;height:41px;line-height:41px;font-size:13.5px}

/* certifications */
.certs{position:absolute;top:2579px;left:0;width:1200px;height:340px;background:var(--mist)}
.certs .section-title{top:36px;color:var(--blue)}
.cert{position:absolute;top:138px;display:flex;align-items:center}
.cert-badge{width:132px;height:132px;border-radius:50%;background:var(--gold);flex:none}
.cert-badge.alt{background:var(--orange)}
.cert-text{margin-left:18px;font-size:16.5px;font-weight:500;line-height:20px}

/* footer */
.site-footer{position:absolute;top:2894px;left:0;width:1200px;height:327px;background:var(--blue);color:var(--white)}
.footer-wedge{position:absolute;left:0;top:-28px;width:1200px;height:30px;background:var(--blue);clip-path:polygon(0 100%,100% 0,100% 100%)}
.footer-brand{position:absolute;left:0;right:0;top:52px;display:flex;justify-content:center;align-items:center;gap:14px}
.footer-brand .brand-mark{width:54px;height:54px;background:var(--white)}
.footer-brand .brand-name{color:var(--white);font-size:34px;letter-spacing:3px;font-weight:700}
.footer-nav{position:absolute;left:0;right:0;top:158px;display:flex;justify-content:center;gap:30px;font-size:14px;font-weight:500}
.footer-nav a.active{font-weight:800}
.follow{position:absolute;left:0;right:0;top:214px;display:flex;justify-content:center;align-items:center;gap:12px;font-size:13.5px;font-weight:500}
.social{width:26px;height:26px;border-radius:50%;background:var(--white);display:block}
.copyright{position:absolute;left:0;right:0;top:270px;text-align:center;font-size:11.5px}
</style>
</head>
<body>

<header class="site-header">
  <a class="brand" href="#"><span class="brand-mark"></span><span class="brand-name">KEYSTONE<br>DELIVERY</span></a>
  <nav class="main-nav">
    <a class="active" href="#">HOME</a>
    <a href="#">ABOUT ME</a>
    <a href="#">SERVICES</a>
    <a href="#" style="margin-left:37px">CERTIFICATION</a>
    <a href="#">PROJECTS</a>
    <a href="#">CONTACT</a>
  </nav>
</header>

<section class="hero">
  <div class="hero-photo" role="img" aria-label="Portrait of Jordan Ellis in a blue plaid suit, with scattered orange and blue squares"></div>
  <div class="hero-band"></div>
  <div class="eyebrow"><span class="eyebrow-tag">ABOUT ME</span><span class="eyebrow-line"></span></div>
  <h1 class="hero-name">Jordan Ellis</h1>
  <div class="hero-rule"></div>
  <div class="hero-copy">
    <p>Jordan Ellis is the Owner of Keystone Delivery Partners, LLC and serves as Principal Lead Consultant on waterfall and agile contract opportunities.</p>
    <p>Keystone Delivery Partners, LLC has engaged on a contract basis with Vantage 400 companies across various industries including banking and credit unions, global supply chain, and international food distribution.</p>
  </div>
  <a class="btn-solid" href="#">READ MORE</a>
</section>

<section class="services">
  <h2 class="section-title">SERVICES</h2>

  <div class="service" style="left:128px;top:160px">
    <svg class="service-icon" viewBox="0 0 54 54" fill="none" stroke="#fff" stroke-width="3"><path d="M6 4h22l10 10v34H6z" fill="#fff"/><path d="M12 20h18M12 28h14M12 36h10" stroke="#0094D4"/><circle cx="38" cy="40" r="8" fill="#fff" stroke="#0094D4"/><circle cx="38" cy="40" r="3" fill="#0094D4" stroke="none"/></svg>
    <h3 class="service-title">Project &amp;<br>Program Management</h3>
    <p class="service-text">There are many variations of passages of Lorem Ipsum avail able, but the majority have suff ered alteration in some form, by injected humour, or rando mised words which don't. . If you are going to use a passage of Lorem Ipsum.</p>
    <a class="btn-outline" href="#">READ MORE</a>
  </div>

  <div class="service" style="left:466px;top:160px">
    <svg class="service-icon" viewBox="0 0 54 54" fill="none" stroke="#fff" stroke-width="3"><path d="M8 27a19 19 0 0 1 33-13M46 27a19 19 0 0 1-33 13"/><path d="M41 6v9h-9M13 48v-9h9"/><rect x="19" y="17" width="16" height="20" rx="2" fill="#fff"/><path d="M23 24h8M23 30h8" stroke="#0094D4"/></svg>
    <h3 class="service-title">Project<br>Management</h3>
    <p class="service-text">There are many variations of passages of Lorem Ipsum avail able, but the majority have suff ered alteration in some form, by injected humour, or rando mised words which don't. . If you are going to use a passage of Lorem Ipsum.</p>
    <a class="btn-outline" href="#">READ MORE</a>
  </div>

  <div class="service" style="left:802px;top:160px">
    <svg class="service-icon" viewBox="0 0 54 54" fill="none" stroke="#fff" stroke-width="3"><path d="M25 8a21 21 0 1 0 21 21H25z" fill="#fff"/><path d="M30 4a20 20 0 0 1 20 20H30z"/><path d="M34 32h16l-8 14z"/></svg>
    <h3 class="service-title">Quality Assurance<br>Analysis</h3>
    <p class="service-text">There are many variations of passages of Lorem Ipsum avail able, but the majority have suff ered alteration in some form, by injected humour, or rando mised words which don't. . If you are going to use a passage of Lorem Ipsum.</p>
    <a class="btn-outline" href="#">READ MORE</a>
  </div>

  <div class="service" style="left:128px;top:566px">
    <svg class="service-icon" viewBox="0 0 54 54" fill="none" stroke="#fff" stroke-width="3"><rect x="5" y="6" width="30" height="42" fill="#fff"/><path d="M10 16h4M18 16h12M10 25h4M18 25h12M10 34h4M18 34h8" stroke="#0094D4"/><circle cx="42" cy="34" r="6"/><path d="M32 50c0-6 5-9 10-9s10 3 10 9z" fill="#fff"/></svg>
    <h3 class="service-title">Strategic Management<br>Consulting</h3>
    <p class="service-text">There are many variations of passages of Lorem Ipsum avail able, but the majority have suff ered alteration in some form, by injected humour, or rando mised words which don't. . If you are going to use a passage of Lorem Ipsum.</p>
    <a class="btn-outline" href="#">READ MORE</a>
  </div>

  <div class="service" style="left:466px;top:566px">
    <svg class="service-icon" viewBox="0 0 60 54" fill="none" stroke="#fff" stroke-width="3"><rect x="22" y="4" width="34" height="28"/><path d="M30 12h8v6h-8zM42 18h8v6h-8z"/><path d="M39 32l-6 18M39 32l6 18"/><circle cx="9" cy="10" r="4" fill="#fff"/><path d="M5 18h8v14M5 18v32M13 32v18M13 22l12-6"/></svg>
    <h3 class="service-title">Planning &amp;<br>Scheduling</h3>
    <p class="service-text">There are many variations of passages of Lorem Ipsum avail able, but the majority have suff ered alteration in some form, by injected humour, or rando mised words which don't. . If you are going to use a passage of Lorem Ipsum.</p>
    <a class="btn-outline" href="#">READ MORE</a>
  </div>

  <div class="service" style="left:802px;top:566px">
    <svg class="service-icon" viewBox="0 0 66 56" fill="none" stroke="#fff" stroke-width="3"><path d="M6 4h38a4 4 0 0 1 4 4v20a4 4 0 0 1-4 4H20l-10 8v-8H6a4 4 0 0 1-4-4V8a4 4 0 0 1 4-4z" fill="#fff"/><path d="M12 14h26M12 22h18" stroke="#0094D4"/><path d="M52 20h8a4 4 0 0 1 4 4v16a4 4 0 0 1-4 4h-2v8l-10-8H34a4 4 0 0 1-4-4v-4"/></svg>
    <h3 class="service-title">Consulting<br>Business</h3>
    <p class="service-text">There are many variations of passages of Lorem Ipsum avail able, but the majority have suff ered alteration in some form, by injected humour, or rando mised words which don't. . If you are going to use a passage of Lorem Ipsum.</p>
    <a class="btn-outline" href="#">READ MORE</a>
  </div>

  <div class="services-wedge"></div>
</section>

<section class="projects">
  <h2 class="section-title">PAST <span class="accent">PROJECTS</span></h2>

  <div class="project" style="left:128px;top:108px;background:linear-gradient(160deg,#4a4c50 0%,#5d5a4e 55%,#7a6f55 100%)" role="img" aria-label="Chalkboard task board covered in sticky notes"><span class="project-label">PROJECT 1</span></div>
  <div class="project" style="left:447px;top:108px;background:linear-gradient(160deg,#3a3c40 0%,#26282b 55%,#4b4d51 100%)" role="img" aria-label="Magnifying glass over agile methodology words"><span class="project-label">PROJECT 2</span></div>
  <div class="project" style="left:765px;top:108px;background:linear-gradient(160deg,#e8eef4 0%,#cdd8e3 55%,#a7b8c9 100%)" role="img" aria-label="Businessman facing a large project schedule chart"><span class="project-label">PROJECT 3</span></div>

  <div class="project" style="left:128px;top:361px;background:linear-gradient(160deg,#5d86ac 0%,#34597e 55%,#1d3552 100%)" role="img" aria-label="Hands typing on a laptop with document overlay"><span class="project-label">PROJECT 4</span></div>
  <div class="project" style="left:447px;top:361px;background:linear-gradient(160deg,#d6e0ea 0%,#aabdd1 55%,#7893b2 100%)" role="img" aria-label="Notebook, pen and tablet on printed charts"><span class="project-label">PROJECT 5</span></div>
  <div class="project" style="left:765px;top:361px;background:linear-gradient(160deg,#eceded 0%,#d7dadd 55%,#b9bec4 100%)" role="img" aria-label="Hand sketching website wireframes"><span class="project-label">PROJECT 6</span></div>

  <div class="project" style="left:128px;top:612px;background:linear-gradient(160deg,#2a2d33 0%,#1b1d22 55%,#44474e 100%)" role="img" aria-label="Laptop screen showing code"><span class="project-label">PROJECT 7</span></div>
  <div class="project" style="left:447px;top:612px;background:linear-gradient(160deg,#8e8e8c 0%,#4d5a70 55%,#2c3c55 100%)" role="img" aria-label="Business person with floating bar chart graphics"><span class="project-label">PROJECT 8</span></div>
  <div class="project" style="left:765px;top:612px;background:linear-gradient(160deg,#8c7a66 0%,#b7a68f 55%,#dcd6ce 100%)" role="img" aria-label="Laptop with analytics dashboard on a wooden desk"><span class="project-label">PROJECT 9</span></div>

  <a class="btn-solid" href="#">VIEW ALL PROJECTS</a>
</section>

<section class="certs">
  <h2 class="section-title">CERTIFICATIONS</h2>
  <div class="cert" style="left:130px"><span class="cert-badge" role="img" aria-label="Certification badge"></span><span class="cert-text">Certified<br>Sprint Facilitator</span></div>
  <div class="cert" style="left:424px"><span class="cert-badge alt" role="img" aria-label="Certification badge"></span><span class="cert-text">Certified Backlog<br>Owner</span></div>
  <div class="cert" style="left:752px"><span class="cert-badge" role="img" aria-label="Certification badge"></span><span class="cert-text">Advanced - Certified<br>Sprint Facilitator</span></div>
</section>

<footer class="site-footer">
  <div class="footer-wedge"></div>
  <div class="footer-brand"><span class="brand-mark"></span><span class="brand-name">KEYSTONE DELIVERY</span></div>
  <nav class="footer-nav">
    <a class="active" href="#">HOME</a>
    <a href="#">ABOUT ME</a>
    <a href="#">SERVICES</a>
    <a href="#" style="margin-left:8px">CERTIFICATION</a>
    <a href="#">PROJECTS</a>
    <a href="#">CONTACT</a>
  </nav>
  <div class="follow">FOLLOW US
    <a class="social" href="#" aria-label="Social profile one"></a>
    <a class="social" href="#" aria-label="Social profile two"></a>
    <a class="social" href="#" aria-label="Social profile three"></a>
  </div>
  <p class="copyright">Copyright © 2022 All Rights Reserved</p>
</footer>

</body>
</html>
```